Plenko - Shoe Fitting App : Foot scanning app, 3D reconstruction and Fit recommandation.

We are a startup that has developed a 3D scanning App that compares the 3d reconstructed foot to the 3D Last (mould) of a shoe to find the best match and recommend a shoe size with a graphical representation of the fit on a reconstructed foot without texturing. The challenge of this app is to have a simple and intuitive onboarding of the user with clean and crisp ui and a simple tutorial for foot scanning. 3D representation of the fit is also key. What you see is what you feel is what we would like to achieve.

Target Market(s)

Sneaker Brands and athletic shoes brands

Industry/Entity Type

Footwear

Font styles to use
Other font styles liked:
• Oswald or Droid Serif

Colors
0094D4
00A9DD
6FCCEA
C7EBF8
E9F6FB

Requirements
Must have
• Simple intuitive UI to onboard the customer to scan his bare foot (please look at attached image on how to scan the foot). You must flip your phone so that the screen is facing your foot. Start at 40cm distance form the front of your foot and turn 360% slowly to capture the foot while you feel the aptic of the iPhone. That needs to be presented with a simple animation that the user can easily understand and skip if he is a returning customer and knows how to do that. the rest of the UI is to present the result of the scanned foot for the user to use to get his fit and size. The other must have is the final result screen. Where the user will a representation of the foot (snug, loose ) of different predefined areas of the foot so he can choose the fit that he likes and not necessarily the size that we suggest. Must match website design (https://www.plenko.example)
Nice to have
• An animation of the whole process (scan-compare 3d foot with 3d shoe last(or mould) and get the 3D result of the best fit + associated size. Optionaly, an option to play with your foot and transform it (avatar like with accessories and colours)
Should not have
• Too many colours. Too much text. No gender type. No race type.

```html
<!DOCTYPE html>
<html lang="en">
<head>
<meta charset="utf-8">
<title>Plenko – Final Result</title>
<link rel="stylesheet" href="https://fonts.googleapis.com/css2?family=Inter:wght@400;500;700;800&display=swap">
<style>
  :root {
    --board-bg: #363a3b;
    --screen-bg: #ffffff;
    --ink: #111111;
    --muted: #6b6b6b;
    --faint: #d9d9d9;
    --tab-bg: #e2e2e2;
    --tab-active: #c7f0f2;
    --glow: #dcebc6;
    --home-bar: #1f3f35;
    --white: #ffffff;
  }
  * { box-sizing: border-box; margin: 0; padding: 0; }
  html, body { width: 1200px; height: 957px; overflow: hidden; }
  body {
    background: var(--board-bg);
    font-family: "Inter", sans-serif;
    position: relative;
  }

  .phone-screen {
    position: absolute;
    left: 186px; top: 131px;
    width: 321px; height: 695px;
    background: var(--screen-bg);
    border-radius: 26px;
    overflow: hidden;
  }
  .status-time {
    position: absolute; left: 25px; top: 13px;
    font-size: 14px; font-weight: 600; color: var(--ink);
  }
  .status-icons { position: absolute; right: 18px; top: 16px; }
  .nav-back { position: absolute; left: 22px; top: 55px; }
  .nav-title {
    position: absolute; left: 0; right: 0; top: 55px;
    text-align: center; font-size: 11px; color: var(--ink);
  }
  .foot-model {
    position: absolute; left: 49px; top: 112px;
    width: 220px; height: 172px;
    border-radius: 40% 50% 30% 55%;
    background: radial-gradient(ellipse at 60% 55%, #b9bf95 0%, #a9b283 40%, #d8e7c9 75%, rgba(230,242,220,0) 100%);
  }
  .view-360 { position: absolute; left: 248px; top: 297px; }

  .size-systems {
    position: absolute; left: 0; right: 0; top: 380px;
    display: flex; justify-content: center; gap: 4px;
  }
  .size-systems span {
    width: 28px; height: 27px; border-radius: 4px;
    background: var(--tab-bg); color: #555;
    font-size: 9.5px; display: flex; align-items: center; justify-content: center;
  }
  .size-systems .is-active { background: var(--tab-active); }
  .slider-hint {
    position: absolute; left: 0; right: 0; top: 421px;
    text-align: center; font-size: 13px; color: var(--muted);
  }
  .size-glow {
    position: absolute; left: 0; right: 0; top: 604px; height: 67px;
    background: radial-gradient(ellipse at 50% 100%, var(--glow) 0%, rgba(240,246,232,0.6) 45%, rgba(255,255,255,0) 80%);
    border-bottom: 1px solid #e6eed8;
  }
  .size-wheel { position: absolute; left: 0; right: 0; top: 0; text-align: center; color: var(--faint); font-weight: 300; }
  .size-wheel span { position: absolute; left: 0; right: 0; line-height: 1; }
  .size-wheel .is-selected { color: var(--ink); font-weight: 400; }
  .fit-note {
    position: absolute; left: 0; right: 0; top: 631px;
    text-align: center; font-size: 13px; color: var(--muted);
  }
  .home-bar {
    position: absolute; left: 104px; top: 674px;
    width: 110px; height: 4px; border-radius: 2px; background: var(--home-bar);
  }

  .brand-name {
    position: absolute; left: 666px; width: 400px; top: 230px;
    text-align: center; color: var(--white);
    font-size: 118px; font-weight: 800; letter-spacing: -4px; line-height: 1;
  }
  .headline {
    position: absolute; left: 620px; width: 500px; top: 420px;
    text-align: center; color: var(--white);
    font-size: 72px; font-weight: 700; letter-spacing: -3px; line-height: 1;
  }
  .summary {
    position: absolute; left: 580px; width: 570px; top: 577px;
    text-align: center; color: var(--white);
    font-size: 28.5px; font-weight: 700; letter-spacing: -1px; line-height: 36px;
  }
</style>
</head>
<body>
  <section class="phone-screen">
    <div class="status-time">9:41</div>
    <svg class="status-icons" width="63" height="11" viewBox="0 0 63 11">
      <rect x="0" y="7" width="3" height="4" rx="0.5" fill="#111"/>
      <rect x="4.5" y="5" width="3" height="6" rx="0.5" fill="#111"/>
      <rect x="9" y="3" width="3" height="8" rx="0.5" fill="#111"/>
      <rect x="13.5" y="0.5" width="3" height="10.5" rx="0.5" fill="#111"/>
      <path d="M23 4 a9 9 0 0 1 12 0 M25.5 6.5 a5 5 0 0 1 7 0" stroke="#111" stroke-width="1.6" fill="none"/>
      <circle cx="29" cy="9.3" r="1.4" fill="#111"/>
      <rect x="41" y="1" width="19" height="9" rx="2.5" fill="#111"/>
      <rect x="61" y="4" width="1.5" height="3" rx="0.7" fill="#111"/>
    </svg>
    <svg class="nav-back" width="10" height="16" viewBox="0 0 10 16"><path d="M8 1 L2 8 L8 15" stroke="#111" stroke-width="1.8" fill="none" stroke-linecap="round" stroke-linejoin="round"/></svg>
    <div class="nav-title">SnugFit</div>

    <div class="foot-model" role="img" aria-label="3D model of a bare foot with fit areas tinted green for good fit and red for pressure points"></div>
    <svg class="view-360" width="29" height="29" viewBox="0 0 29 29" aria-label="Rotate 360 degrees">
      <circle cx="14.5" cy="14.5" r="12" stroke="#666" stroke-width="1.4" fill="none"/>
      <ellipse cx="14.5" cy="14.5" rx="14" ry="6" stroke="#666" stroke-width="1.2" fill="none" transform="rotate(-35 14.5 14.5)"/>
      <text x="14.5" y="17.5" text-anchor="middle" font-size="8" font-weight="700" fill="#555" font-family="Inter, sans-serif">360</text>
    </svg>

    <div class="size-systems">
      <span class="is-active">UK</span><span>US</span><span>EU</span><span>IT</span>
    </div>
    <p class="slider-hint">Slide to choose the best fit for you!</p>

    <div class="size-glow"></div>
    <div class="size-wheel">
      <span style="top:468px;font-size:9px;color:#efefef">5</span>
      <span style="top:484px;font-size:15px">6</span>
      <span style="top:501px;font-size:24px;color:#cfcfcf">7</span>
      <span class="is-selected" style="top:519px;font-size:40px">8</span>
      <span style="top:560px;font-size:24px;color:#cfcfcf">9</span>
      <span style="top:584px;font-size:16px;color:#e6e6e6">10</span>
      <span style="top:601px;font-size:9px;color:#f0f0f0">11</span>
    </div>

    <p class="fit-note">Perfect balance of comfort and support.</p>
    <div class="home-bar"></div>
  </section>

  <div class="brand-name">Plenko</div>
  <h1 class="headline">Final Result</h1>
  <p class="summary">Displays areas of concern on a foot and represents the fit using 3D modeling.</p>
</body>
</html>
```